Online interactive tutorial for year 2 to year 12 students in Australia

Website design for a new online tutorial for year 2 to year 12 students in Australia.

- The tutorial will be conducted via live webcam and within a dedicated interactive space
- The tutorial will be provided by high scoring undergraduates studying in top Australian universities.
- The tutors will be going through interviews & assessments & only top students are allowed to apply.
- Parents will do search and select tutor and have short 15 mins video interaction with potential tutors before booking them for their children for tutoring.
- hourly cost of booking (no monthly subscription or no hour limits)
- Tutors will have their own profile

Please see the attached for detailed page functionality.

The look and feel of the design must consider the following:
- must be educational but not dull and should stand out
- must appeal to younger generation - tutees (8-18 years), tutors (19-25), parents (30-50).
- Ideas for Logos (brivora.com.au but not confirmed)

Target Market(s)

tutees (8-18 years), tutors (19-25 years), parents (30-50 years).

Industry/Entity Type

Education

Coding

Coded - Design and coding required

Number of Pages Required

5+ page

Font styles to use
Serif

Requirements
Must have
• The look and feel of the design must consider the following:
• - must be educational but not dull and should stand out
• - must appeal to younger generation - tutees (8-18 years), tutors (19-25), parents (30-50).
Should not have
• Dullness

```html
<!DOCTYPE html>
<html lang="en">
<head>
<meta charset="utf-8">
<title>Brivora – Online Training for Kids</title>
<link href="https://fonts.googleapis.com/css2?family=Oswald:wght@400;500&family=Open+Sans:wght@400;600&display=swap" rel="stylesheet">
<style>
:root{
  --blue:#1aafd6;
  --heading-blue:#1d9dc6;
  --orange:#f8a81b;
  --red:#e0393b;
  --green:#9dc11d;
  --green-btn:#8fbf2a;
  --grey-band:#f2f2f2;
  --text:#555;
  --dark:#3a3a3a;
  --darker:#2f2f2f;
  --purple:#6a2fc0;
  --icon-green:#8cc63f;
  --icon-blue:#1aa6d6;
  --icon-green2:#3aa33a;
}
*{box-sizing:border-box;margin:0;padding:0}
html,body{width:1200px;height:3600px;overflow:hidden;background:#fff}
body{font-family:"Open Sans",Arial,sans-serif;color:var(--text);position:relative}
.h{font-family:"Oswald",Arial,sans-serif;font-weight:400;text-transform:uppercase}
.abs{position:absolute}

/* header */
.topstripe{left:0;top:0;width:1200px;height:6px;background:linear-gradient(90deg,#1aafd6 0 20%,#f8a81b 20% 40%,#9dc11d 40% 60%,#e0393b 60% 80%,#6a2fc0 80%)}
.header-bg{left:0;top:6px;width:1200px;height:640px;background:linear-gradient(180deg,#e3f5fb,#ffffff 40%)}
.brand{left:75px;top:32px;display:flex;align-items:center;gap:12px}
.brand-mark{width:30px;height:30px;background:var(--blue);flex:none}
.brand-name{font-family:"Open Sans",Arial,sans-serif;font-size:36px;font-weight:600;color:#3a3a3a;line-height:1}
.brand-line{left:75px;top:80px;font-family:"Open Sans",Arial,sans-serif;font-size:16px;font-weight:400;color:#666}
.top-btns{right:74px;top:22px;display:flex;gap:10px}
.top-btn{font-family:"Oswald",sans-serif;font-size:15px;color:#fff;padding:0 18px;height:42px;line-height:42px;text-transform:uppercase}
.phone{right:74px;top:78px;font-family:"Oswald",sans-serif;font-size:23px;color:#444;display:flex;align-items:center;gap:10px}
.phone b{color:var(--red);font-weight:400}

.nav{left:74px;top:127px;width:1052px;height:60px;background:linear-gradient(180deg,#22bde3,#129ec6);display:flex;align-items:center;padding:0 22px;justify-content:space-between}
.nav a{font-family:"Oswald",sans-serif;color:#fff;font-size:17px;text-decoration:none;text-transform:uppercase}

.hero{left:74px;top:187px;width:1052px;height:456px;overflow:hidden}
.hero-photo{width:100%;height:100%;background:linear-gradient(100deg,#c9d7df 0%,#e6ecef 35%,#b59279 60%,#6b4a3a 100%)}
.hero-curve{left:0;bottom:0;width:1052px;height:40px}
.hero-title{left:34px;top:150px;font-size:50px;line-height:56px;color:var(--red);font-weight:500}
.dots{left:34px;top:375px;display:flex;gap:6px}
.dots i{width:10px;height:10px;border-radius:50%;background:#222;display:block}
.dots i:first-child{background:#fff}

/* section titles */
.sec-title{width:1200px;left:0;text-align:center;font-size:28px;color:var(--heading-blue)}
.sec-title::after{content:"";display:block;width:46px;height:3px;background:#888;margin:12px auto 0}
.sec-sub{width:1200px;left:0;text-align:center;font-size:15px;color:#666}

.welcome-text{left:84px;width:1032px;top:770px;text-align:center;font-size:14.6px;line-height:29px;color:#666}
.btn-orange{background:var(--orange);color:#fff;font-family:"Oswald",sans-serif;text-transform:uppercase;text-align:center}
.read-more{left:524px;top:907px;width:152px;height:53px;line-height:53px;font-size:17px}

.services{left:0;top:1027px;width:1200px;height:461px;background:var(--grey-band)}
.svc{display:flex;align-items:flex-start;gap:20px;width:500px;font-size:14.5px;line-height:24px;color:#555}
.svc-icon{width:56px;height:56px;border-radius:50%;flex:none;display:flex;align-items:center;justify-content:center}

.video{left:166px;top:1661px;width:868px;height:380px;border:4px solid #cfcfcf;background:linear-gradient(120deg,#3c4a58,#7a8a92 40%,#c9b08a 70%,#8a6a52)}
.play{left:566px;top:1820px;width:68px;height:50px;background:#fff;border-radius:10px}

.tutors{left:0;top:2093px;width:1200px;height:590px;background:var(--green)}
.card{top:2230px;width:243px;height:398px;background:#fff;padding:14px 17px;text-align:center}
.card-photo{width:208px;height:192px;background:linear-gradient(180deg,#d8d8d8,#a9a9a9)}
.card-name{font-size:17px;color:var(--red);margin-top:22px}
.card-text{font-size:14px;line-height:21px;color:#555;margin-top:8px}
.more{width:134px;height:38px;line-height:38px;font-size:14px;margin:14px auto 0}
.arrow{top:2395px}

/* scheduler */
.sched-title{left:74px;top:2735px;font-size:30px;color:var(--heading-blue)}
.event{left:74px;width:530px;border-bottom:1px solid #e2e2e2;padding-bottom:14px}
.event-date{font-family:"Oswald",sans-serif;font-size:17px;color:var(--red);text-transform:uppercase}
.event-text{font-size:14.5px;line-height:24px;color:#555;margin-top:6px}
.event-text b{color:var(--blue);font-weight:600}

.cal{left:614px;top:2743px;width:512px}
.cal-head{display:flex;height:44px}
.cal-head .t1{flex:1;background:var(--blue);color:#fff;font-size:21px;line-height:44px;padding-left:18px}
.cal-head .t2{width:156px;background:var(--orange);color:#fff;font-size:21px;line-height:44px;padding-left:14px;display:flex;justify-content:space-between;padding-right:10px}
.cal-grid{display:grid;grid-template-columns:repeat(7,1fr);gap:2px;background:#fff;margin-top:2px}
.cal-grid .dn{background:#555;color:#fff;font-size:12px;height:26px;line-height:26px;text-align:center;font-family:"Oswald",sans-serif}
.cal-grid .d{background:#eee;height:52px;line-height:52px;text-align:center;font-size:15px;color:#444}
.cal-grid .r{color:var(--red);font-weight:600}

/* footer */
.footer{left:0;top:3139px;width:1200px;height:461px;background:var(--dark)}
.f-title{font-family:"Oswald",sans-serif;font-size:16px;color:var(--green);text-transform:uppercase}
.f-links{list-style:none;font-size:14px;color:#ddd;line-height:30.5px;margin-top:16px}
.f-text{font-size:14px;line-height:22px;color:#ddd}
.news{display:flex;margin-top:18px}
.news span{width:270px;height:44px;background:#fff;font-size:13px;color:#333;line-height:44px;padding-left:14px}
.news i{width:64px;height:44px;background:var(--blue);display:flex;align-items:center;justify-content:center}
.social{display:flex;gap:22px;margin-top:24px}
.social i{width:16px;height:16px;border-radius:50%;background:#ddd;display:block}
.field{width:332px;background:#fff;font-size:13px;color:#333;padding:0 14px;height:44px;line-height:44px;margin-top:10px}
.send{width:136px;height:42px;line-height:42px;font-size:15px;margin:14px 0 0 196px}
.f-bottom{left:0;top:3528px;width:1200px;height:72px;background:var(--darker)}
.copy{left:74px;top:3558px;font-size:13px;color:#ccc}
.cards{right:74px;top:3552px;display:flex;gap:10px}
.cards i{display:block;width:38px;height:24px;border-radius:3px;background:#e6e6e6}
</style>
</head>
<body>

<div class="abs header-bg"></div>
<div class="abs topstripe"></div>

<div class="abs brand">
  <span class="brand-mark"></span>
  <span class="brand-name">Brivora</span>
</div>
<div class="abs brand-line">Online Training for Kids</div>

<div class="abs top-btns">
  <div class="top-btn" style="background:var(--green-btn)">Tutor Registration</div>
  <div class="top-btn" style="background:var(--orange)">Parent Registration</div>
  <div class="top-btn" style="background:var(--blue)">Student Log In</div>
</div>

<div class="abs phone">
  <svg width="20" height="20" viewBox="0 0 24 24"><path fill="#444" d="M6.6 10.8a15.1 15.1 0 0 0 6.6 6.6l2.2-2.2c.3-.3.7-.4 1-.2 1.1.4 2.3.6 3.6.6.6 0 1 .4 1 1V20c0 .6-.4 1-1 1A17 17 0 0 1 3 4c0-.6.4-1 1-1h3.5c.6 0 1 .4 1 1 0 1.3.2 2.5.6 3.6.1.3 0 .7-.2 1z"/></svg>
  <span>CALL US: <b>1-800-555-0142</b></span>
</div>

<nav class="abs nav">
  <a>Home</a><a>About Us</a><a>Services</a><a>Tutor Profile</a><a>How It Works</a><a>Scheduler</a><a>Testimonials</a><a>Contact Us</a>
</nav>

<div class="abs hero">
  <div class="hero-photo" role="img" aria-label="Photo of a mother and young daughter using a tablet together at home"></div>
  <div class="abs hero-title h">Vestibulum vel metus<br>sit amet dignissim</div>
  <div class="abs dots"><i></i><i></i><i></i><i></i></div>
  <svg class="abs hero-curve" viewBox="0 0 1052 40" preserveAspectRatio="none"><path d="M0 40 L0 18 Q526 -18 1052 18 L1052 40 Z" fill="#fff"/></svg>
</div>

<!-- welcome -->
<div class="abs sec-title h" style="top:690px">Welcome to our website</div>
<p class="abs welcome-text">Aliquam molestie, mi et imperdiet euismod, dui purus auctor tellus, et interdum lacus lectus et ante. Sed accumsan sollicitudin sapien, sit amet adipiscing turpis gravida ac. In congue, neque ac lobortis volutpat, libero mauris varius mi, vitae suscipit ipsum ligula vitae risus. Duis aliquam nibh a dui iaculis viverra id a velit. Vivamus egestas risus in magna varius commodo. Sed semper viverra egestas. Etiam pretium porttitor lectus, vel ornare neque porta volutpat.</p>
<div class="abs btn-orange read-more">Read More</div>

<!-- services -->
<div class="abs services"></div>
<div class="abs sec-title h" style="top:1068px">Our Services</div>
<p class="abs sec-sub" style="top:1148px">Aliquam molestie, mi et imperdiet euismod, dui purus auctor tellus, et interdum lacus lectus et ante.</p>

<div class="abs svc" style="left:74px;top:1206px">
  <div class="svc-icon" style="background:var(--icon-green)"><svg width="28" height="22" viewBox="0 0 28 22"><rect x="5" y="2" width="18" height="13" rx="1" fill="none" stroke="#fff" stroke-width="2.4"/><rect x="1" y="17" width="26" height="3" fill="#fff"/></svg></div>
  <div>The tutorial will be conducted via live webcam and within a dedicated interactive space..</div>
</div>
<div class="abs svc" style="left:74px;top:1288px">
  <div class="svc-icon" style="background:var(--red)"><svg width="26" height="24" viewBox="0 0 26 24"><rect x="2" y="2" width="22" height="20" fill="none" stroke="#fff" stroke-width="2"/><rect x="6" y="12" width="3" height="7" fill="#fff"/><rect x="11.5" y="8" width="3" height="11" fill="#fff"/><rect x="17" y="5" width="3" height="14" fill="#fff"/></svg></div>
  <div>The tutorial will be provided by high scoring undergraduates studying in top Australian universities..</div>
</div>
<div class="abs svc" style="left:74px;top:1370px">
  <div class="svc-icon" style="background:var(--icon-blue)"><svg width="30" height="22" viewBox="0 0 30 22"><circle cx="15" cy="6" r="4.5" fill="#fff"/><path d="M7 21c0-5 3.5-8 8-8s8 3 8 8z" fill="#fff"/><circle cx="6" cy="8" r="3" fill="#fff"/><circle cx="24" cy="8" r="3" fill="#fff"/><path d="M0 19c0-3.5 2.5-6 6-6 1 0 2 .3 2.6.7C7 15.3 6 17 6 19z" fill="#fff"/><path d="M30 19c0-3.5-2.5-6-6-6-1 0-2 .3-2.6.7 1.6 1.6 2.6 3.3 2.6 5.3z" fill="#fff"/></svg></div>
  <div>The tutors will be going through interviews &amp; assessments &amp; only top students are allowed to apply..</div>
</div>

<div class="abs svc" style="left:622px;top:1206px">
  <div class="svc-icon" style="background:var(--orange)"><svg width="24" height="24" viewBox="0 0 24 24"><circle cx="10" cy="10" r="6.5" fill="none" stroke="#fff" stroke-width="2.6"/><path d="M15 15l6 6" stroke="#fff" stroke-width="3" stroke-linecap="round"/></svg></div>
  <div>Parents will do search and select tutor and have short 15 mins video interaction withpotential tutors before booking them for their children for tutoring.</div>
</div>
<div class="abs svc" style="left:622px;top:1288px">
  <div class="svc-icon" style="background:var(--purple)"><svg width="24" height="24" viewBox="0 0 24 24"><circle cx="12" cy="12" r="9.5" fill="none" stroke="#fff" stroke-width="2.4"/><path d="M12 6v6l4 3" fill="none" stroke="#fff" stroke-width="2.4" stroke-linecap="round"/></svg></div>
  <div>Hourly cost of booking (no monthly subscription or no hour limits)..</div>
</div>
<div class="abs svc" style="left:622px;top:1370px">
  <div class="svc-icon" style="background:var(--icon-green2)"><svg width="22" height="24" viewBox="0 0 22 24"><circle cx="11" cy="7" r="5.5" fill="#fff"/><path d="M1 23c0-6 4.5-9.5 10-9.5S21 17 21 23z" fill="#fff"/></svg></div>
  <div>Tutors will have their own profile..</div>
</div>

<!-- how it works -->
<div class="abs sec-title h" style="top:1533px">How It Works</div>
<p class="abs sec-sub" style="top:1614px">Aliquam molestie, mi et imperdiet euismod, dui purus auctor tellus, et interdum lacus lectus et ante.</p>
<div class="abs video" role="img" aria-label="Video still of a teacher and a group of children gathered around a computer in a classroom"></div>
<div class="abs play"><svg width="68" height="50" viewBox="0 0 68 50"><path d="M27 14 L45 25 L27 36 Z" fill="#333"/></svg></div>

<!-- tutor profiles -->
<div class="abs tutors"></div>
<div class="abs sec-title h" style="top:2132px;color:#fff">Tutor Profiles</div>
<svg class="abs arrow" style="left:44px" width="14" height="24" viewBox="0 0 14 24"><path d="M11 3 L3 12 L11 21" fill="none" stroke="#fff" stroke-width="3.5"/></svg>
<svg class="abs arrow" style="left:1142px" width="14" height="24" viewBox="0 0 14 24"><path d="M3 3 L11 12 L3 21" fill="none" stroke="#fff" stroke-width="3.5"/></svg>

<div class="abs card" style="left:74px">
  <div class="card-photo" role="img" aria-label="Portrait photo of a male tutor"></div>
  <div class="card-name h">Name Heading</div>
  <div class="card-text">Aenean a nibh eget turpis vehicula tempus ac sed massa congue..</div>
  <div class="btn-orange more">More Info</div>
</div>
<div class="abs card" style="left:345px">
  <div class="card-photo" role="img" aria-label="Portrait photo of a female tutor"></div>
  <div class="card-name h">Name Heading</div>
  <div class="card-text">Aenean a nibh eget turpis vehicula tempus ac sed massa congue..</div>
  <div class="btn-orange more">More Info</div>
</div>
<div class="abs card" style="left:614px">
  <div class="card-photo" role="img" aria-label="Portrait photo of a male tutor in a suit"></div>
  <div class="card-name h">Name Heading</div>
  <div class="card-text">Aenean a nibh eget turpis vehicula tempus ac sed massa congue..</div>
  <div class="btn-orange more">More Info</div>
</div>
<div class="abs card" style="left:883px">
  <div class="card-photo" role="img" aria-label="Portrait photo of a female tutor"></div>
  <div class="card-name h">Name Heading</div>
  <div class="card-text">Aenean a nibh eget turpis vehicula tempus ac sed massa congue..</div>
  <div class="btn-orange more">More Info</div>
</div>

<!-- scheduler -->
<div class="abs sched-title h">Scheduler</div>
<div class="abs event" style="top:2806px">
  <div class="event-date">Sep 05, 2016</div>
  <div class="event-text">Aenean a nibh eget turpis vehicula tempus ac sed massa congue habitant morbi tristique senectus et netus..<b>Read More</b></div>
</div>
<div class="abs event" style="top:2910px">
  <div class="event-date">Sep 14, 2016</div>
  <div class="event-text">Aenean a nibh eget turpis vehicula tempus ac sed massa congue habitant morbi tristique senectus et netus..<b>Read More</b></div>
</div>
<div class="abs event" style="top:3014px;border-bottom:none">
  <div class="event-date">Sep 19, 2016</div>
  <div class="event-text">Aenean a nibh eget turpis vehicula tempus ac sed massa congue habitant morbi tristique senectus et netus..<b>Read More</b></div>
</div>

<div class="abs cal">
  <div class="cal-head h">
    <div class="t1">Calander</div>
    <div class="t2"><span>Sep 2016</span><svg width="34" height="44" viewBox="0 0 34 44"><path d="M11 15 L5 22 L11 29" fill="none" stroke="#fff" stroke-width="3"/><path d="M23 15 L29 22 L23 29" fill="none" stroke="#fff" stroke-width="3"/></svg></div>
  </div>
  <div class="cal-grid">
    <div class="dn">S</div><div class="dn">M</div><div class="dn">T</div><div class="dn">W</div><div class="dn">T</div><div class="dn">F</div><div class="dn">S</div>
    <div class="d"></div><div class="d"></div><div class="d"></div><div class="d"></div><div class="d">1</div><div class="d">2</div><div class="d">3</div>
    <div class="d">4</div><div class="d r">5</div><div class="d">6</div><div class="d">7</div><div class="d">8</div><div class="d r">9</div><div class="d">10</div>
    <div class="d">11</div><div class="d">12</div><div class="d">13</div><div class="d r">14</div><div class="d">15</div><div class="d">16</div><div class="d">17</div>
    <div class="d">18</div><div class="d">19</div><div class="d">20</div><div class="d">21</div><div class="d">22</div><div class="d">23</div><div class="d">24</div>
    <div class="d">25</div><div class="d">26</div><div class="d">27</div><div class="d">28</div><div class="d">29</div><div class="d">30</div><div class="d"></div>
  </div>
</div>

<!-- footer -->
<footer class="abs footer"></footer>
<div class="abs" style="left:74px;top:3188px">
  <div class="f-title">Quick Links</div>
  <ul class="f-links"><li>Home</li><li>About Us</li><li>Services</li><li>Tutor Profile</li><li>How It Works</li><li>Scheduler</li><li>Testimonials</li><li>Contact Us</li></ul>
</div>
<div class="abs" style="left:343px;top:3188px;width:340px">
  <div class="f-title">Newsletter Sign Up</div>
  <p class="f-text" style="margin-top:14px">Vestibulum ante ipsum primis in faucibus orci luctus et ultrices posuere</p>
  <div class="news"><span>Enter Email Address</span><i><svg width="20" height="18" viewBox="0 0 20 18"><path d="M1 8 L19 1 L15 17 L9 12 Z" fill="#fff"/></svg></i></div>
  <div class="f-title" style="margin-top:28px">Follow Us</div>
  <div class="social"><i></i><i></i><i></i><i></i><i></i><i></i></div>
</div>
<div class="abs" style="left:794px;top:3188px">
  <div class="f-title">Contact Us</div>
  <div class="field" style="margin-top:20px">Name</div>
  <div class="field">Email Address</div>
  <div class="field" style="height:80px">Message</div>
  <div class="btn-orange send">Send</div>
</div>
<svg class="abs" style="left:0;top:3508px" width="1200" height="22" viewBox="0 0 1200 22" preserveAspectRatio="none"><path d="M0 22 Q600 -10 1200 22 Z" fill="#2f2f2f"/></svg>
<div class="abs f-bottom"></div>
<div class="abs copy">Copyright © 2016. Company Name. All Right Reserved</div>
<div class="abs cards"><i></i><i></i><i></i><i></i><i></i></div>

</body>
</html>
```